PHGCCUL re-branding website and logo

We are looking for a new webpage design and logo our current page address is www.phgccul-example.org. We want to create a new design using PHGCCUL Pinewood and Harbour Growers Co-operative Credit Union limited and another with the purposed new name PHFC Pinewood and Harbour Financial Co-operative, the color scheme is purple and burnt orange. Our new logo and webpage should communicate change and growth purposed theme continuing our legacy here to server past, present and future generations. Our idea for the logo is a live shot of hands of different ages in a circle holding a tree

Target Market(s)

Everyone

Contact Information for Business Card

Company Name
Telephone number
Address
slot to enter employee info

Logo Text

(P & H) Pinewood And Harbour Financial Co-operative

Coding

Coded - Design and coding required

Number of Pages Required

2 page

Colors
f37122
fbed22
6b449b

Requirements
Must have
• links for social media

```html
<!DOCTYPE html>
<html lang="en">
<head>
<meta charset="utf-8">
<title>Pinewood and Harbour Financial Co-operative</title>
<link rel="stylesheet" href="https://fonts.googleapis.com/css2?family=Raleway:wght@300;400;500;600;700&family=Open+Sans:ital,wght@0,400;0,600;1,400&display=swap">
<style>
:root{
  --orange:#f37122;
  --yellow:#d9cf0c;
  --purple:#6b449b;
  --black:#000;
  --footer-bottom:#0d0d0d;
  --grey-bg:#f2f2f2;
  --text:#222;
  --muted:#444;
  --white:#fff;
  --brand-dot:#5b5f4a;
}
*{box-sizing:border-box;margin:0;padding:0}
html,body{width:1200px;height:2329px;overflow:hidden}
body{position:relative;font-family:"Open Sans",Arial,sans-serif;color:var(--text);background:var(--white)}

/* brand: plain circle + name in one colour, one weight */
.brand{position:absolute;display:flex;align-items:center;gap:12px}
.brand-dot{width:66px;height:66px;border-radius:50%;background:var(--brand-dot);flex:none}
.brand-name{font-family:"Raleway",sans-serif;font-weight:600;color:var(--white);line-height:1}
.brand-name .short{display:block;font-size:32px;letter-spacing:2px}
.brand-name .full{display:block;font-size:7px;letter-spacing:1px;text-transform:uppercase;margin-top:8px;width:130px;line-height:10px}

/* header */
.site-header{position:absolute;left:0;top:0;width:1200px;height:129px;background:var(--black)}
.site-header .brand{left:161px;top:28px}
.contact-top{position:absolute;top:28px;font-size:14px;color:var(--white)}
.main-nav{position:absolute;top:80px;left:489px;display:flex;gap:38px;font-family:"Raleway",sans-serif;font-size:12.5px;font-weight:500;color:var(--white)}
.main-nav .active{color:#f4c20d;position:relative}
.main-nav .active::after{content:"";position:absolute;left:50%;top:37px;margin-left:-6px;border:6px solid transparent;border-bottom-color:#f4c20d}

/* hero */
.hero{position:absolute;left:0;top:129px;width:1200px;height:486px;background:linear-gradient(120deg,#6b5a48 0%,#a89a8c 35%,#d6d2cc 55%,#8b8178 80%,#3c3834 100%)}
.hero-title{position:absolute;top:160px;width:1200px;text-align:center;color:var(--white);font-family:"Raleway",sans-serif}
.hero-title .line1{font-weight:300;font-size:45px;display:block;line-height:60px}
.hero-title .line2{font-weight:600;font-size:53px;display:block;line-height:62px}
.hero-arrow{position:absolute;top:195px}

/* features */
.tile{position:absolute;top:666px;width:206px;height:206px;border-bottom:6px solid #111;color:var(--white);text-align:center}
.tile svg{margin-top:30px}
.tile h3{font-family:"Raleway",sans-serif;font-weight:400;font-size:18px;margin-top:14px}
.tile p{font-size:10.5px;line-height:17px;margin:8px auto 0;width:160px;opacity:.9}
.tile-credit{left:161px;background:var(--orange)}
.tile-products{left:385px;background:var(--yellow)}
.tile-tools{left:607px;background:var(--purple)}
.quick-link{position:absolute;left:830px;width:207px;height:46px;background:var(--black);color:var(--white);font-family:"Raleway",sans-serif;font-size:13.5px;display:flex;align-items:center;gap:12px;padding-left:14px}
.quick-link::before{content:"";position:absolute;left:0;top:0;width:4px;height:100%}
.ql-1::before{background:#555}.ql-2::before{background:var(--orange)}.ql-3::before{background:var(--yellow)}.ql-4::before{background:var(--purple)}

/* rates */
.rates{position:absolute;left:0;top:936px;width:1200px;height:453px;background:var(--grey-bg);border-top:1px solid #e2e2e2}
.section-title{font-family:"Raleway",sans-serif;font-weight:700;color:var(--text)}
.rates .section-title{position:absolute;left:161px;top:56px;font-size:25px}
.rate-card{position:absolute;top:110px;width:207px}
.rate-photo{width:207px;height:139px}
.rate-card h4{font-family:"Raleway",sans-serif;font-weight:500;font-size:15px;margin-top:12px}
.rate-value{font-family:"Raleway",sans-serif;font-weight:700;font-size:16px;color:var(--orange);margin-top:10px}
.rate-value small{font-size:7px;font-weight:400;color:#666;vertical-align:middle;margin-left:2px}
.rate-card p{font-size:10.5px;line-height:19px;color:var(--muted);margin-top:6px}

/* testimonials */
.testimonials{position:absolute;left:0;top:1389px;width:1200px;height:339px;background:linear-gradient(90deg,#e2661b,#e86c1f 50%,#d9621a)}
.testimonials .section-title{position:absolute;top:38px;width:1200px;text-align:center;color:var(--white);font-size:25px}
.testimonial-quote{position:absolute;left:325px;top:104px;width:550px;text-align:center;color:var(--white);font-style:italic;font-size:11.5px;line-height:21px}
.testimonial-quote b{font-family:Georgia,serif;font-size:22px;font-style:normal;vertical-align:-6px}
.avatar{position:absolute;left:515px;top:214px;width:76px;height:76px;border-radius:50%;background:radial-gradient(circle,#cbb8a8,#6e5a4c);border:3px solid var(--white)}
.author{position:absolute;left:602px;top:228px;color:var(--white);font-family:"Raleway",sans-serif;font-weight:600;font-size:14px;line-height:21px}

/* news */
.news .section-title{position:absolute;top:1770px;width:1200px;text-align:center;font-weight:600;font-size:26px;color:#333}
.news-item{position:absolute;top:1860px;width:255px}
.news-head{display:flex;gap:10px}
.news-date{font-family:"Raleway",sans-serif;color:var(--orange);text-align:center;border-right:1px solid #ccc;padding-right:10px;line-height:21px}
.news-date span{display:block;font-size:15px}
.news-date strong{display:block;font-size:22px;font-weight:700}
.news-head h4{font-family:"Raleway",sans-serif;font-weight:500;font-size:16px;line-height:23px;color:#222}
.news-item p{font-size:10.5px;line-height:20px;color:var(--muted);margin-top:22px}

/* footer */
.site-footer{position:absolute;left:0;top:2052px;width:1200px;height:224px;background:var(--black);color:var(--white)}
.site-footer .brand{left:161px;top:66px}
.footer-col{position:absolute;top:40px}
.footer-col h5{font-family:"Raleway",sans-serif;font-weight:600;font-size:14.5px;margin-bottom:16px}
.footer-col li{list-style:none;font-size:10.5px;line-height:20px;display:flex;align-items:center;gap:8px;color:#e8e8e8}
.footer-col svg{flex:none}
.footer-bottom{position:absolute;left:0;top:2276px;width:1200px;height:53px;background:var(--footer-bottom)}
.social{position:absolute;left:164px;top:14px;display:flex;gap:6px}
.social a{width:25px;height:25px;border:1.5px solid var(--white);border-radius:50%;display:block}
.copyright{position:absolute;right:163px;top:19px;font-size:10.5px;color:var(--white)}
</style>
</head>
<body>

<header class="site-header">
  <div class="brand">
    <span class="brand-dot"></span>
    <span class="brand-name"><span class="short">P &amp; H</span><span class="full">Pinewood &amp; Harbour Financial Co-operative</span></span>
  </div>
  <div class="contact-top" style="left:717px">Phone: (555) 010-2200</div>
  <div class="contact-top" style="left:912px">Fax: (555) 010-2291</div>
  <nav class="main-nav">
    <span class="active">HOME</span>
    <span>APPLY FOR A LOAN</span>
    <span>BECOME A MEMBER</span>
    <span>LOCATIONS</span>
    <span>ABOUT US</span>
  </nav>
</header>

<section class="hero" role="img" aria-label="Photo of a desk with a laptop, charts and hands reviewing financial reports">
  <h1 class="hero-title"><span class="line1">Pinewood and Harbour</span><span class="line2">Financial Co-operative</span></h1>
  <svg class="hero-arrow" style="left:32px" width="34" height="72" viewBox="0 0 34 72"><polyline points="32,2 2,36 32,70" fill="none" stroke="#fff" stroke-width="2"/></svg>
  <svg class="hero-arrow" style="left:1134px" width="34" height="72" viewBox="0 0 34 72"><polyline points="2,2 32,36 2,70" fill="none" stroke="#fff" stroke-width="2"/></svg>
</section>

<section class="features">
  <div class="tile tile-credit">
    <svg width="80" height="62" viewBox="0 0 80 62"><rect x="4" y="14" width="64" height="42" rx="6" fill="none" stroke="#fff" stroke-width="5"/><rect x="14" y="4" width="62" height="40" rx="6" fill="var(--orange)" stroke="#fff" stroke-width="5"/><rect x="14" y="14" width="62" height="8" fill="#fff"/><rect x="22" y="32" width="16" height="4" fill="#fff"/></svg>
    <h3>My Credit Union</h3>
    <p>Sed ut perlospiciatis undemlori natusr sit volupta lortem.</p>
  </div>
  <div class="tile tile-products">
    <svg width="70" height="62" viewBox="0 0 70 62"><circle cx="42" cy="20" r="12" fill="none" stroke="#fff" stroke-width="6" stroke-dasharray="5 3"/><circle cx="42" cy="20" r="4" fill="#fff"/><path d="M4 44h14l14 6h16l16-10v8L48 60H22L4 54z" fill="#fff"/></svg>
    <h3>Products &amp; Services</h3>
    <p>Sed ut perlospiciatis undemlori natusr sit volupta lortem.</p>
  </div>
  <div class="tile tile-tools">
    <svg width="72" height="62" viewBox="0 0 72 62"><rect x="8" y="42" width="7" height="18" fill="#fff"/><rect x="20" y="34" width="7" height="26" fill="#fff"/><rect x="32" y="38" width="7" height="22" fill="#fff"/><rect x="44" y="26" width="7" height="34" fill="#fff"/><rect x="56" y="18" width="7" height="42" fill="#fff"/><polyline points="4,34 24,18 38,26 62,6" fill="none" stroke="#fff" stroke-width="4"/><polygon points="52,4 66,2 64,16" fill="#fff"/></svg>
    <h3>Tools &amp; Benefits</h3>
    <p>Sed ut perlospiciatis undemlori natusr sit volupta lortem.</p>
  </div>
  <div class="quick-link ql-1" style="top:666px"><svg width="14" height="20" viewBox="0 0 14 20"><rect x="1" y="1" width="12" height="18" rx="6" fill="none" stroke="#fff" stroke-width="1.5"/><line x1="7" y1="3" x2="7" y2="8" stroke="#fff" stroke-width="1.5"/></svg>Internet Teller Login</div>
  <div class="quick-link ql-2" style="top:719px"><svg width="16" height="20" viewBox="0 0 16 20"><rect x="1" y="1" width="12" height="16" fill="none" stroke="#fff" stroke-width="1.5"/><line x1="4" y1="6" x2="10" y2="6" stroke="#fff"/><line x1="4" y1="10" x2="10" y2="10" stroke="#fff"/></svg>Apply For A Loan</div>
  <div class="quick-link ql-3" style="top:773px"><svg width="16" height="20" viewBox="0 0 16 20"><circle cx="8" cy="6" r="4" fill="#fff"/><path d="M1 19c0-6 14-6 14 0z" fill="#fff"/></svg>Become a Member</div>
  <div class="quick-link ql-4" style="top:826px"><svg width="16" height="20" viewBox="0 0 16 20"><rect x="1" y="1" width="14" height="18" fill="none" stroke="#fff" stroke-width="1.5"/><rect x="3" y="3" width="10" height="4" fill="#fff"/><g fill="#fff"><rect x="3" y="9" width="3" height="3"/><rect x="7" y="9" width="3" height="3"/><rect x="11" y="9" width="2" height="3"/><rect x="3" y="14" width="3" height="3"/><rect x="7" y="14" width="3" height="3"/><rect x="11" y="14" width="2" height="3"/></g></svg>Financial Calculator</div>
</section>

<section class="rates">
  <h2 class="section-title">FEATURED RATES</h2>
  <article class="rate-card" style="left:161px">
    <div class="rate-photo" role="img" aria-label="Photo of hands signing a loan document and handing over keys" style="background:linear-gradient(135deg,#c9a27a,#e6ddd2 60%,#9d8a78)"></div>
    <h4>Consumer Loans</h4>
    <div class="rate-value">9.00%<small>APR*</small></div>
    <p>Sed ut perlospiciatis unde omloreiste natus error sit volupta lortem accusan tium doloremque laudloan tium.</p>
  </article>
  <article class="rate-card" style="left:385px">
    <div class="rate-photo" role="img" aria-label="Photo of two men shaking hands in a car showroom" style="background:linear-gradient(135deg,#8a949c,#d9dde0 55%,#4d5257)"></div>
    <h4>New Auto/Motorcycle</h4>
    <div class="rate-value">7.00%<small>APR*</small></div>
    <p>Sed ut perlospiciatis unde omloreiste natus error sit volupta lortem accusan tium doloremque laudloan tium.</p>
  </article>
  <article class="rate-card" style="left:607px">
    <div class="rate-photo" role="img" aria-label="Photo of car keys being handed over in front of a blue car" style="background:linear-gradient(135deg,#c9d6e2,#3a6fb0 55%,#7d8c99)"></div>
    <h4>Used Auto/Motorcycle</h4>
    <div class="rate-value">11.75%<small>APR*</small></div>
    <p>Sed ut perlospiciatis unde omloreiste natus error sit volupta lortem accusan tium doloremque laudloan tium.</p>
  </article>
  <article class="rate-card" style="left:830px">
    <div class="rate-photo" role="img" aria-label="Photo of a couple meeting an advisor about a mortgage" style="background:linear-gradient(135deg,#5a5048,#d8d2ca 55%,#8a9ab0)"></div>
    <h4>Mortgages</h4>
    <div class="rate-value">8.25%<small>APR*</small></div>
    <p>Sed ut perlospiciatis unde omloreiste natus error sit volupta lortem accusan tium doloremque laudloan tium.</p>
  </article>
</section>

<section class="testimonials" role="img" aria-label="Orange-toned background photo of growing stacks of coins with seedlings">
  <h2 class="section-title">TESTIMONIALS</h2>
  <blockquote class="testimonial-quote"><b>&ldquo;</b> Sed ut perspiciatis unde omnis iste natus error sit voluptatelorem accusan tium doloremque laudantium, totam rem aperiam, eaque ipsa quaeab illo inven tore veritatis et quasi architecto beatae vitae dicta sunt expli caboeo enim ipsam voluptatem quia voluptas sit aspernatur aut odit aut euia cns euntur magni dolores eosui rtatem quia voluptas sit aspernatur sit aspernatur aatione. <b>&rdquo;</b></blockquote>
  <div class="avatar" role="img" aria-label="Portrait of the member giving the testimonial"></div>
  <div class="author">Alan Reyes,<br>City Name</div>
</section>

<section class="news">
  <h2 class="section-title">NEWS &amp; EVENTS</h2>
  <article class="news-item" style="left:161px">
    <div class="news-head"><div class="news-date"><span>FEB</span><strong>20</strong></div><h4>Sed ut perspiciatis ndois iste natus sit olupt.</h4></div>
    <p>Sd ut perspiciatis unde omnis isteiste natus errort vo luptatem accusantium doloremque liS ut pertis un de omnis isteiste natus Sed ut persluptatem us antium doloremque liS ut persciatis un.</p>
  </article>
  <article class="news-item" style="left:477px">
    <div class="news-head"><div class="news-date"><span>FEB</span><strong>20</strong></div><h4>Sed ut perspiciatis ndois iste natus sit olupt.</h4></div>
    <p>Sd ut perspiciatis unde omnis isteiste natus errort vo luptatem accusantium doloremque liS ut pertis un de omnis isteiste natus Sed ut persluptatem us antium doloremque liS ut persciatis un.</p>
  </article>
  <article class="news-item" style="left:790px">
    <div class="news-head"><div class="news-date"><span>FEB</span><strong>20</strong></div><h4>Sed ut perspiciatis ndois iste natus sit olupt.</h4></div>
    <p>Sd ut perspiciatis unde omnis isteiste natus errort vo luptatem accusantium doloremque liS ut pertis un de omnis isteiste natus Sed ut persluptatem us antium doloremque liS ut persciatis un.</p>
  </article>
</section>

<footer class="site-footer">
  <div class="brand">
    <span class="brand-dot"></span>
    <span class="brand-name"><span class="short">P &amp; H</span><span class="full">Pinewood &amp; Harbour Financial Co-operative</span></span>
  </div>

  <div class="footer-col" style="left:402px">
    <h5>Nassau</h5>
    <ul>
      <li><svg width="8" height="11" viewBox="0 0 8 11"><path d="M4 0a4 4 0 0 1 4 4c0 3-4 7-4 7S0 7 0 4a4 4 0 0 1 4-4z" fill="var(--orange)"/></svg>Harbour Road &amp; Pinewood Ave.</li>
      <li><svg width="9" height="10" viewBox="0 0 9 10"><path d="M2 0l2 3-1 1c1 2 2 3 3 3l1-1 2 2-1 2C4 10 0 6 0 1z" fill="var(--orange)"/></svg>Phone: (555) 010-2200</li>
      <li><svg width="10" height="10" viewBox="0 0 10 10"><rect x="0" y="3" width="10" height="7" fill="var(--orange)"/><rect x="2" y="0" width="6" height="3" fill="var(--orange)"/></svg>Fax: (555) 010-2291</li>
      <li><svg width="10" height="8" viewBox="0 0 10 8"><rect width="10" height="8" fill="var(--orange)"/><polyline points="0,0 5,4 10,0" fill="none" stroke="#000"/></svg>Email:info@phfc-example.org</li>
    </ul>
  </div>
  <div class="footer-col" style="left:636px">
    <h5>Freeport, Grand Bahama</h5>
    <ul>
      <li><svg width="8" height="11" viewBox="0 0 8 11"><path d="M4 0a4 4 0 0 1 4 4c0 3-4 7-4 7S0 7 0 4a4 4 0 0 1 4-4z" fill="var(--orange)"/></svg>#14 Seabreeze Lane</li>
      <li><svg width="9" height="10" viewBox="0 0 9 10"><path d="M2 0l2 3-1 1c1 2 2 3 3 3l1-1 2 2-1 2C4 10 0 6 0 1z" fill="var(--orange)"/></svg>Phone: (555) 010-3189</li>
      <li><svg width="10" height="10" viewBox="0 0 10 10"><rect x="0" y="3" width="10" height="7" fill="var(--orange)"/><rect x="2" y="0" width="6" height="3" fill="var(--orange)"/></svg>Fax: (555) 010-3136</li>
      <li><svg width="10" height="8" viewBox="0 0 10 8"><rect width="10" height="8" fill="var(--orange)"/><polyline points="0,0 5,4 10,0" fill="none" stroke="#000"/></svg>Email:info@phfc-example.org</li>
    </ul>
  </div>
  <div class="footer-col" style="left:871px">
    <h5>Abaco</h5>
    <ul>
      <li><svg width="8" height="11" viewBox="0 0 8 11"><path d="M4 0a4 4 0 0 1 4 4c0 3-4 7-4 7S0 7 0 4a4 4 0 0 1 4-4z" fill="var(--orange)"/></svg>Maple Court Plaza</li>
      <li><svg width="9" height="10" viewBox="0 0 9 10"><path d="M2 0l2 3-1 1c1 2 2 3 3 3l1-1 2 2-1 2C4 10 0 6 0 1z" fill="var(--orange)"/></svg>Phone: (555) 010-4613</li>
      <li><svg width="10" height="10" viewBox="0 0 10 10"><rect x="0" y="3" width="10" height="7" fill="var(--orange)"/><rect x="2" y="0" width="6" height="3" fill="var(--orange)"/></svg>Fax: (555) 010-4612</li>
      <li><svg width="10" height="8" viewBox="0 0 10 8"><rect width="10" height="8" fill="var(--orange)"/><polyline points="0,0 5,4 10,0" fill="none" stroke="#000"/></svg>Email:info@phfc-example.org</li>
    </ul>
  </div>
</footer>

<div class="footer-bottom">
  <nav class="social" aria-label="Social media links">
    <a href="#" aria-label="Social link 1"></a>
    <a href="#" aria-label="Social link 2"></a>
    <a href="#" aria-label="Social link 3"></a>
    <a href="#" aria-label="Social link 4"></a>
  </nav>
  <p class="copyright">Copyright © 2017 Pinewood and Harbour Financial Co-operative. All Rights Reserved.</p>
</div>

</body>
</html>
```